Business card for my new company (Accounting firm)

I need a business card for my new business Brightwell Advisory and Ledger SA. Our services are accounting, tax, audit and financial management. Our customers are small companies, start-ups and new companies. The final design has to show financial security, trust and growth. Please find our logo attached to the business card. Text for the business card: Brightwell Advisory and Ledger SA Tomas Varenholt Director and Founder Certified Accountant Tel. 022 418 57 34 tv@clairevalconseil.ch www.clairevalconseil.ch Rue des Vergières 27 1201 Geneva
Target Market(s)
Our customers are small companies, start-ups and new companies.
Industry/Entity Type
Finance And Accounting
Contact Information for Business Card
Claireval Conseil et Comptes SA
Tomas Varenholt
Directeur et Fondateur
Expert-comptable diplômé
Tél. 022 418 57 34
tv@clairevalconseil.ch
www.clairevalconseil.ch
Rue des Vergières 27
1201 Genève

```html
<!DOCTYPE html>
<html lang="fr">
<head>
<meta charset="utf-8">
<title>Claireval Conseil et Comptes SA – Carte de visite</title>
<link href="https://fonts.googleapis.com/css2?family=Raleway:wght@400;500;600;700&display=swap" rel="stylesheet">
<style>
  :root {
    --backdrop: #5e5e5e;
    --card-white: #f3f3f3;
    --brand-blue: #1d5d8f;
    --brand-navy: #1f5a86;
    --bar-dark: #3a3a3a;
    --text-grey: #4a4a4a;
    --wordmark: #3b3b3b;
    --back-blue: #1f5f8e;
  }
  * { margin: 0; padding: 0; box-sizing: border-box; }
  html, body {
    width: 1200px; height: 960px; overflow: hidden;
    background: var(--backdrop);
    font-family: "Raleway", Arial, sans-serif;
  }
  .canvas { position: relative; width: 1200px; height: 960px; }

  .card {
    position: absolute; left: 270px; width: 662px; height: 378px;
    box-shadow: 0 6px 14px rgba(0,0,0,0.45);
  }
  .card-front { top: 73px; background: var(--card-white); overflow: hidden; }
  .card-back { top: 508px; background: var(--back-blue); }

  .edge-accent { position: absolute; left: 0; top: 0; }

  .holder { position: absolute; left: 59px; top: 64px; }
  .holder-name {
    font-weight: 700; font-size: 20px; color: var(--brand-blue);
    letter-spacing: 0.2px; text-transform: uppercase;
  }
  .holder-role { font-size: 15px; color: var(--text-grey); line-height: 19px; margin-top: 2px; }

  .company { position: absolute; left: 60px; top: 204px; font-size: 15px; line-height: 19px; }
  .company-name { color: var(--brand-blue); font-weight: 500; }
  .company-address { color: var(--text-grey); }

  .contact { position: absolute; left: 59px; top: 283px; list-style: none; font-size: 15px; color: var(--text-grey); }
  .contact li { display: flex; align-items: center; height: 19px; }
  .contact svg { width: 12px; height: 12px; margin-right: 10px; fill: none; stroke: var(--brand-navy); stroke-width: 1.4; }

  .wordmark {
    position: absolute; right: 62px; top: 268px; text-align: right;
    color: var(--wordmark); font-weight: 600; text-transform: uppercase;
  }
  .wordmark-mark { display: inline-block; width: 22px; height: 22px; background: var(--brand-blue); margin-bottom: 10px; }
  .wordmark-name { font-size: 36px; letter-spacing: 2px; line-height: 38px; }
  .wordmark-tag { font-size: 12.5px; letter-spacing: 1.6px; margin-top: 4px; }

  .back-pattern {
    position: absolute; inset: 0;
    background: linear-gradient(135deg, #21628f 0%, #1c5a87 100%);
  }
  .back-wordmark {
    position: absolute; left: 64px; top: 262px;
    color: #ffffff; font-weight: 600; font-size: 18px; letter-spacing: 1.5px;
    text-transform: uppercase;
  }
</style>
</head>
<body>
<main class="canvas">

  <section class="card card-front" aria-label="Recto de la carte">
    <svg class="edge-accent" width="40" height="378" viewBox="0 0 40 378">
      <polygon points="0,68 38,82 14,112 14,145 0,145" fill="var(--brand-blue)"/>
      <rect x="0" y="145" width="14" height="233" fill="var(--bar-dark)"/>
    </svg>

    <div class="holder">
      <h1 class="holder-name">Tomas Varenholt</h1>
      <p class="holder-role">Directeur et Fondateur</p>
      <p class="holder-role">Expert - Comptable Diplômé</p>
    </div>

    <address class="company" style="font-style:normal">
      <div class="company-name">Claireval Conseil et Comptes SA</div>
      <div class="company-address">Rue des Vergières 27</div>
      <div class="company-address">1201 Genève</div>
    </address>

    <ul class="contact">
      <li><svg viewBox="0 0 12 12"><path d="M2 1.5l2 0 1 2.5-1.2 1a6 6 0 0 0 3.2 3.2l1-1.2 2.5 1 0 2a1 1 0 0 1-1 1A9 9 0 0 1 1 2.5a1 1 0 0 1 1-1z"/></svg>022 418 57 34</li>
      <li><svg viewBox="0 0 12 12"><rect x="1" y="2.5" width="10" height="7"/><path d="M1 2.5l5 4 5-4"/></svg>tv@clairevalconseil.ch</li>
      <li><svg viewBox="0 0 12 12"><circle cx="6" cy="6" r="5"/><path d="M1 6h10M6 1c-2.5 3-2.5 7 0 10M6 1c2.5 3 2.5 7 0 10"/></svg>www.clairevalconseil.ch</li>
    </ul>

    <div class="wordmark">
      <span class="wordmark-mark"></span>
      <div class="wordmark-name">Claireval</div>
      <div class="wordmark-tag">Conseil et Comptes</div>
    </div>
  </section>

  <section class="card card-back" aria-label="Verso de la carte">
    <div class="back-pattern" role="img" aria-label="Motif répété en relief de la marque sur fond bleu"></div>
    <div class="back-wordmark">Claireval</div>
  </section>

</main>
</body>
</html>
```